New Business Card Design Project LORVANTI-Italy

we are LORVANTI-Italy
our company in the market for 3 years we are luxury cosmetic company and its about time for a facelift :)
i will like to have elegant luxurious and unique business card
that will give the person that get it a unique, luxurious and elegant impression
I'm VERY OPEN FOR NEW IDEAS , even duo i add a few files of things that i see on line and i like them

i add my logo as well
my website is LORVANTI.COM
(if you would like to see the main style that we have)

Target Market(s)

adult that have money :)

Industry/Entity Type

Business

Contact Information for Business Card

Name - Dario Lorvanti
Position - CEO and CO Founder
address - 4817 E Halvern
telephone - 555-384-1926
email - dario@lorvanti.com
fax - 555-384-1926
website - LORVANTI.COM

Colors
000000
959595
fbee3e
ffffff

Requirements
Must have
• big logo in GOLD color
• elegant look
• impressive
Nice to have
• not must but maybe classy pattern background
• not must but maybe emblem
• maybe clear plastic business card
Should not have
• colors
• images

```html
<!DOCTYPE html>
<html lang="en">
<head>
<meta charset="utf-8">
<title>LORVANTI Italy – Business Card</title>
<link href="https://fonts.googleapis.com/css2?family=Open+Sans:wght@400;600&display=swap" rel="stylesheet">
<style>
  :root {
    --backdrop: #2e2825;
    --card-black: #141414;
    --gold: #c9a240;
    --white: #f2f2f2;
    --grey: #959595;
    --rule: #bdbdbd;
  }
  * { margin: 0; padding: 0; box-sizing: border-box; }
  html, body {
    width: 1200px; height: 864px; overflow: hidden;
    background: var(--backdrop);
    font-family: "Open Sans", Arial, sans-serif;
  }
  .canvas { position: relative; width: 1200px; height: 864px; }

  .card {
    position: absolute;
    width: 560px; height: 320px;
    background: var(--card-black);
    border-radius: 4px;
    box-shadow: 0 12px 30px rgba(0,0,0,.45);
    overflow: hidden;
  }

  /* front: emblem side */
  .card-front { left: 60px; top: 80px; }
  .front-mark {
    position: absolute; left: 50%; top: 46%;
    transform: translate(-50%, -50%);
    display: flex; flex-direction: column; align-items: center; gap: 14px;
  }
  .mark-circle {
    width: 120px; height: 120px; border-radius: 50%;
    border: 3px solid var(--gold);
  }
  .brand-name {
    color: var(--gold); font-weight: 600; font-size: 30px;
    letter-spacing: 4px;
  }
  .front-web {
    position: absolute; left: 36px; bottom: 30px;
    color: var(--grey); font-size: 15px; letter-spacing: 4px;
  }

  /* back: contact side */
  .card-back { left: 580px; top: 464px; }
  .person {
    position: absolute; left: 34px; top: 60px;
  }
  .person-name { color: var(--gold); font-weight: 600; font-size: 21px; }
  .person-title { color: var(--white); font-size: 15px; margin-top: 2px; }
  .contacts {
    position: absolute; left: 34px; top: 128px;
    list-style: none;
  }
  .contacts li {
    display: flex; align-items: center; gap: 8px;
    color: var(--white); font-size: 13px; line-height: 21px;
  }
  .contacts svg { width: 13px; height: 13px; fill: var(--gold); }
  .divider {
    position: absolute; left: 34px; right: 34px; top: 212px;
    height: 2px; background: var(--rule);
  }
  .back-mark {
    position: absolute; right: 40px; top: 40px;
    display: flex; flex-direction: column; align-items: center; gap: 10px;
  }
  .back-mark .mark-circle { width: 78px; height: 78px; }
  .back-mark .brand-name { font-size: 32px; letter-spacing: 3px; }
  .address {
    position: absolute; right: 34px; bottom: 28px; text-align: right;
    color: var(--white); font-size: 15px; line-height: 22px;
  }
  .address .web { font-size: 17px; }
</style>
</head>
<body>
<main class="canvas">
  <section class="card card-front">
    <div class="front-mark">
      <div class="mark-circle"></div>
      <div class="brand-name">LORVANTI</div>
    </div>
    <p class="front-web">www.lorvanti.com</p>
  </section>

  <section class="card card-back">
    <div class="person">
      <p class="person-name">Dario Lorvanti</p>
      <p class="person-title">CEO &amp; CO Founder</p>
    </div>
    <ul class="contacts">
      <li>
        <svg viewBox="0 0 16 16" aria-hidden="true"><path d="M3 1h3l1.5 4-2 1.5a9 9 0 0 0 4 4l1.5-2 4 1.5v3a1 1 0 0 1-1 1A13 13 0 0 1 2 2a1 1 0 0 1 1-1z"/></svg>
        555-384-1926
      </li>
      <li>
        <svg viewBox="0 0 16 16" aria-hidden="true"><path d="M4 1h8v4H4z"/><path d="M1 6h14v7h-3v2H4v-2H1zM5 11v3h6v-3z"/></svg>
        555-384-1926
      </li>
      <li>
        <svg viewBox="0 0 16 16" aria-hidden="true"><path d="M1 3h14v10H1zM2 4l6 5 6-5z" fill-rule="evenodd"/></svg>
        dario@lorvanti.com
      </li>
    </ul>
    <div class="divider"></div>
    <div class="back-mark">
      <div class="mark-circle"></div>
      <div class="brand-name">LORVANTI</div>
    </div>
    <div class="address">
      <p>4817 E Halvern</p>
      <p class="web">WWW.LORVANTI.COM</p>
    </div>
  </section>
</main>
</body>
</html>
```